Business Cards for IT Consulting Company (Managed Service Provider)

I am looking to have some business cards printed and would like some designs. We are an IT Consulting company based in Vancouver BC. I would like a nice clean and modern look to the cards. I have uploaded all the versions of my logo so parts can be used as needed. Here is a snippit from our website homepage:

Quillbrook Networks Ltd. is an IT Solutions Partner located in Vancouver BC, Canada. We offer IT solutions and support to customers in the greater Vancouver Area. With expertise in Microsoft platforms, as well as Linux and Mac OSX and over 12 years experience in the IT industry, Quillbrook Networks is dedicated to offering our clients top quality service and products. We take pride in the solutions we offer our customers. The greatest compliment a client can give us is to recommend our services.

Quillbrook Networks Ltd. offers a wide range of IT services from onsite service to remote support and managed service solutions. This allows clients to choose the support path that best suits their company’s needs. Supporting many different sized companies from small to enterprise level over the past 12 years Quillbrook Networks has the experience and expertise needed to ensure things run smoothly. Allowing our clients to focus on doing business.

Revolutionizing the way IT services are delivered.

Quillbrook Networks is dedicated to providing our clients with IT solutions that work and grow with them for years to come. This philosophy helps save money in the long run instead of replacing equipment constantly. Far too often IT solutions are not well thought out and while possibly solving the problem at hand, require replacement due to growth or quality within a very short time frame. Quillbrook Networks takes pride in providing solutions that will last and be able to accommodate growth without the need for replacement.

Industry/Entity Type

Information Technology

Contact Information for Business Card

Quillbrook Networks Ltd.
(Employee Name)
Eml: (Employees Email Address)
Web: quillbrook.me
Ph: 604-555-0148

Font styles to use
Serif
Sans Serif

Requirements
Must have
• The Company logo and company colors.
Nice to have
• - Our tag line: "Revolutionizing IT Services" or "Revolutionizing the way IT services are delivered."
• - Also I really like the idea of nature and technology together blending which is sort of where my logo came from so integrating that somehow onto the business cards would be great.

```html
<!DOCTYPE html>
<html lang="en">
<head>
<meta charset="utf-8">
<title>Quillbrook Networks Ltd. – Business Cards</title>
<link rel="stylesheet" href="https://fonts.googleapis.com/css2?family=Montserrat:wght@500;600&family=Open+Sans:wght@400&display=swap">
<style>
  :root {
    --brand-blue: #029fd9;
    --map-blue: #2db0e2;
    --ink-grey: #5a5a5c;
    --paper: #ffffff;
    --backdrop: #eceef0;
  }
  * { box-sizing: border-box; margin: 0; padding: 0; }
  html, body {
    width: 1147px;
    height: 1200px;
    overflow: hidden;
    background: var(--backdrop);
  }
  .sheet {
    position: relative;
    width: 1147px;
    height: 1200px;
  }
  .card {
    position: absolute;
    left: 123px;
    width: 900px;
    height: 514px;
    box-shadow: 0 2px 10px rgba(0,0,0,0.12);
  }
  /* Front */
  .card-front {
    top: 40px;
    background: var(--brand-blue);
    color: var(--paper);
  }
  .world-map {
    position: absolute;
    left: 150px;
    top: 70px;
    width: 600px;
    height: 330px;
    border-radius: 40% 45% 38% 42%;
    background: radial-gradient(ellipse at center, rgba(255,255,255,0.16) 0%, rgba(255,255,255,0.05) 60%, rgba(255,255,255,0) 75%);
  }
  .front-brand {
    position: absolute;
    left: 0;
    right: 0;
    top: 185px;
    display: flex;
    align-items: center;
    justify-content: center;
    gap: 22px;
    font-family: "Montserrat", sans-serif;
    font-weight: 600;
  }
  .brand-square {
    width: 62px;
    height: 62px;
    border: 4px solid var(--paper);
  }
  .front-brand .brand-name {
    font-size: 58px;
    line-height: 1;
    letter-spacing: 0.5px;
  }
  .front-url {
    position: absolute;
    right: 60px;
    bottom: 40px;
    font-family: "Open Sans", sans-serif;
    font-size: 20px;
    letter-spacing: 0.5px;
  }
  /* Back */
  .card-back {
    top: 620px;
    background: var(--paper);
    display: flex;
  }
  .back-brand {
    width: 470px;
    display: flex;
    align-items: center;
    justify-content: center;
    gap: 14px;
    font-family: "Montserrat", sans-serif;
    font-weight: 600;
    color: var(--brand-blue);
  }
  .back-brand .brand-square {
    width: 40px;
    height: 40px;
    border: 3px solid var(--brand-blue);
  }
  .back-brand .brand-name {
    font-size: 28px;
    line-height: 1.1;
  }
  .divider {
    width: 14px;
    margin: 90px 0 80px;
    background: linear-gradient(to right, rgba(0,0,0,0.10), rgba(0,0,0,0));
  }
  .contact {
    padding-top: 150px;
    padding-left: 40px;
  }
  .contact-name {
    font-family: "Montserrat", sans-serif;
    font-weight: 600;
    font-size: 29px;
    color: var(--brand-blue);
    margin-bottom: 34px;
  }
  .contact-list { list-style: none; }
  .contact-item {
    display: flex;
    align-items: center;
    gap: 14px;
    font-family: "Open Sans", sans-serif;
    font-size: 24px;
    color: var(--ink-grey);
    margin-bottom: 14px;
  }
  .contact-icon { width: 24px; height: 24px; flex: none; }
</style>
</head>
<body>
<main class="sheet">
  <section class="card card-front" aria-label="Card front">
    <div class="world-map" role="img" aria-label="Faint dotted world map in the background"></div>
    <div class="front-brand">
      <span class="brand-square" aria-hidden="true"></span>
      <span class="brand-name">Quillbrook Networks Ltd.</span>
    </div>
    <p class="front-url">www.quillbrook.me</p>
  </section>

  <section class="card card-back" aria-label="Card back">
    <div class="back-brand">
      <span class="brand-square" aria-hidden="true"></span>
      <span class="brand-name">Quillbrook Networks Ltd.</span>
    </div>
    <div class="divider" aria-hidden="true"></div>
    <div class="contact">
      <h1 class="contact-name">Employee Name</h1>
      <ul class="contact-list">
        <li class="contact-item">
          <svg class="contact-icon" viewBox="0 0 24 24" aria-hidden="true"><rect x="2" y="5" width="20" height="14" fill="var(--brand-blue)"/><path d="M2 5 L12 13 L22 5" fill="none" stroke="#fff" stroke-width="2"/></svg>
          yourmail@email.com
        </li>
        <li class="contact-item">
          <svg class="contact-icon" viewBox="0 0 24 24" aria-hidden="true"><path d="M6 3 L9 3 L10 8 L8 10 C9 13 11 15 14 16 L16 14 L21 15 L21 18 C21 20 19 21 17 21 C9 20 4 15 3 7 C3 5 4 3 6 3 Z" fill="var(--brand-blue)"/></svg>
          604-555-0148
        </li>
        <li class="contact-item">
          <svg class="contact-icon" viewBox="0 0 24 24" aria-hidden="true"><circle cx="12" cy="12" r="10" fill="none" stroke="var(--brand-blue)" stroke-width="2.5"/><path d="M2 12 H22 M12 2 C8 6 8 18 12 22 M12 2 C16 6 16 18 12 22" fill="none" stroke="var(--brand-blue)" stroke-width="1.6"/></svg>
          www.quillbrook.me
        </li>
      </ul>
    </div>
  </section>
</main>
</body>
</html>
```